Company director needs a business card design

I am a semi-retired former senior finance executive who sits on a number of public and private company boards and do some consulting work. I work largely with emerging businesses but deal regularly with top end of town lawyers, bankers etc. I need a thoughtful but relatively conservative design which would also resonate with my younger client base. Some colour would be good. Information limited to name, address, office tel, mobile and email.

Finance

```html
<!DOCTYPE html>
<html lang="en">
<head>
<meta charset="utf-8">
<title>Business Card – Marcus Hale</title>
<link rel="stylesheet" href="https://fonts.googleapis.com/css2?family=Michroma&family=Orbitron:wght@700&display=swap">
<style>
  :root {
    --page-bg: #e9e7e3;
    --card-white: #ffffff;
    --card-shade: #f1f1f1;
    --brand-red: #dc2434;
    --ink-dark: #1b1b1b;
    --band-grey: #bdbdbd;
    --band-black: #111111;
    --text-light: #f7d3d6;
  }
  html, body {
    margin: 0;
    padding: 0;
    width: 1200px;
    height: 800px;
    overflow: hidden;
    background: var(--page-bg);
  }
  .canvas {
    position: relative;
    width: 1200px;
    height: 800px;
  }
  .card {
    position: absolute;
    left: 110px;
    top: 120px;
    width: 980px;
    height: 560px;
    overflow: hidden;
    background: linear-gradient(180deg, var(--card-white) 0%, var(--card-shade) 50%);
    box-shadow: 0 14px 36px rgba(0, 0, 0, 0.18);
    font-family: "Michroma", sans-serif;
  }
  .card__shapes {
    position: absolute;
    inset: 0;
  }
  .card__name-block {
    position: absolute;
    right: 160px;
    top: 106px;
    text-align: right;
  }
  .card__name {
    margin: 0;
    color: var(--brand-red);
    font-family: "Orbitron", sans-serif;
    font-size: 27px;
    font-weight: 700;
    letter-spacing: 1px;
    line-height: 1.1;
  }
  .card__title {
    margin: 4px 0 0;
    color: var(--ink-dark);
    font-size: 13px;
    letter-spacing: 0.6px;
  }
  .contact {
    position: absolute;
    display: flex;
    align-items: center;
    gap: 22px;
    margin: 0;
    font-size: 20px;
    letter-spacing: 1px;
    white-space: nowrap;
  }
  .contact svg { flex: none; }
  .contact--mobile { left: 44px; top: 271px; color: var(--ink-dark); }
  .contact--office { left: 586px; top: 259px; color: var(--card-white); }
  .card__details {
    position: absolute;
    left: 44px;
    top: 428px;
    color: var(--text-light);
  }
  .card__details .contact {
    position: static;
    font-size: 16px;
    gap: 30px;
    margin-bottom: 10px;
  }
</style>
</head>
<body>
<div class="canvas">
  <section class="card" aria-label="Business card front">
    <svg class="card__shapes" width="980" height="560" viewBox="0 0 980 560" aria-hidden="true">
      <rect class="accent-line" x="0" y="124" width="500" height="2" fill="var(--brand-red)"/>
      <rect class="accent-line" x="848" y="124" width="132" height="2" fill="var(--brand-red)"/>
      <rect class="red-field" x="0" y="290" width="980" height="270" fill="var(--brand-red)"/>
      <polygon class="grey-band" points="0,268 520,268 538,300 0,300" fill="var(--band-grey)"/>
      <polygon class="black-band" points="540,256 980,256 980,290 522,290" fill="var(--band-black)"/>
    </svg>

    <div class="card__name-block">
      <h1 class="card__name">MARCUS HALE</h1>
      <p class="card__title">Managing Director</p>
    </div>

    <p class="contact contact--mobile">
      <svg width="16" height="20" viewBox="0 0 16 20" aria-label="Mobile">
        <rect x="1.5" y="1.5" width="13" height="17" rx="2" fill="none" stroke="var(--ink-dark)" stroke-width="2"/>
      </svg>
      <span>0098 7654 321</span>
    </p>

    <p class="contact contact--office">
      <svg width="22" height="20" viewBox="0 0 22 20" aria-label="Office">
        <g fill="var(--card-white)">
          <rect x="4" y="1" width="14" height="2"/>
          <rect x="4" y="1" width="2" height="17"/>
          <rect x="16" y="1" width="2" height="17"/>
          <rect x="10" y="1" width="2" height="17"/>
          <rect x="4" y="7" width="14" height="2"/>
          <rect x="4" y="12" width="14" height="2"/>
          <rect x="0" y="17" width="22" height="2"/>
        </g>
      </svg>
      <span>0098 7654 321</span>
    </p>

    <div class="card__details">
      <p class="contact contact--email">
        <svg width="24" height="16" viewBox="0 0 24 16" aria-label="Email">
          <rect x="1" y="1" width="22" height="14" fill="var(--text-light)"/>
          <polyline points="1,1 12,9 23,1" fill="none" stroke="var(--brand-red)" stroke-width="1.5"/>
        </svg>
        <span>info@yourdomain.com</span>
      </p>
      <p class="contact contact--address">
        <svg width="24" height="18" viewBox="0 0 24 18" aria-label="Address">
          <polygon points="12,1 23,9 20,9 20,17 4,17 4,9 1,9" fill="var(--text-light)"/>
        </svg>
        <span>Address your Inc 00 2nd Ave Millbrook, NJ xxxxx</span>
      </p>
    </div>
  </section>
</div>
</body>
</html>
```